Business Cards Needed for Innovative Healthcare Marketing Company

We are a marketing company focused on healthcare. Our company is all about rebranding yourself renewing your image and generating results. The phoenix stands for "reborn" or "rising" which we provide new brands for our clients we take their old brands and renew it with creativity and innovation. I am looking for a business card with color dimension. I have attached an example of a card I think has the look and feel of what I am trying to accomplish. I like that the card example has black and grey font colors, I like the font placement and the small logo, I really like the use of the colors on the right those are the colors of my logo. My logo is phoenix so maybe incorporating flames similar to that design. I would like the back a solid color maybe red with an opaque version of the logo and website. As a marketing company I am always open to creative liberty!

Target Market(s)

Doctors and business professionals.

Industry/Entity Type

Marketing

Contact Information for Business Card

Valcorne Health Care Marketing
Marla Tenwick- CEO
#(512)638-2974
email-marla@valcorne.com
website- valcorne.com

Font styles to use
Sans Serif

Colors
ec1f27
f37122
ffc214
fbed22
fbf289
f04a50

Requirements
Must have
• The logo and required information
Nice to have
• icons by the information
Should not have
• child like font

```html
<!DOCTYPE html>
<html lang="en">
<head>
<meta charset="utf-8">
<title>Valcorne Health Care Marketing – Business Card</title>
<link rel="stylesheet" href="https://fonts.googleapis.com/css2?family=Open+Sans:wght@300;400;700&display=swap">
<style>
  :root {
    --stage: #2e2e2e;
    --card-white: #ffffff;
    --brand-red: #9e1f24;
    --deep-red: #8c1c22;
    --flame-orange: #f7941d;
    --gold: #f7a325;
    --ink-white: #ffffff;
    --back-black: #000000;
  }
  * { box-sizing: border-box; margin: 0; padding: 0; }
  html, body {
    width: 1200px;
    height: 987px;
    overflow: hidden;
    background: var(--stage);
    font-family: "Open Sans", Arial, sans-serif;
  }
  .card {
    position: absolute;
    left: 293px;
    width: 615px;
    height: 352px;
    overflow: hidden;
  }
  .card--front { top: 125px; background: var(--card-white); }
  .card--back { top: 511px; background: var(--back-black); }

  .front-wave { position: absolute; inset: 0; width: 615px; height: 352px; }

  .brand {
    position: absolute;
    display: flex;
    flex-direction: column;
    align-items: center;
    gap: 14px;
  }
  .brand__dot {
    width: 84px;
    height: 84px;
    border-radius: 50%;
  }
  .brand__name {
    font-weight: 300;
    font-size: 20px;
    line-height: 1.25;
    letter-spacing: 2px;
    text-transform: uppercase;
    text-align: center;
  }
  .card--front .brand { left: 55px; top: 42px; width: 200px; }
  .card--front .brand__dot { background: var(--flame-orange); }
  .card--front .brand__name { color: var(--brand-red); }

  .card--back .brand { left: 0; right: 0; top: 80px; }
  .card--back .brand__dot { background: var(--deep-red); }
  .card--back .brand__name { color: var(--deep-red); }

  .person {
    position: absolute;
    right: 50px;
    top: 166px;
    text-align: right;
  }
  .person__name {
    color: var(--gold);
    font-weight: 700;
    font-size: 23px;
    line-height: 1.2;
  }
  .person__title {
    color: var(--ink-white);
    font-weight: 700;
    font-size: 17px;
    line-height: 1.3;
  }
  .contacts {
    position: absolute;
    right: 28px;
    top: 236px;
    list-style: none;
  }
  .contacts__item {
    display: flex;
    justify-content: flex-end;
    align-items: center;
    gap: 10px;
    height: 24px;
    color: var(--ink-white);
    font-size: 16.5px;
  }
  .contacts__icon { width: 19px; height: 19px; flex: none; }
</style>
</head>
<body>

<section class="card card--front">
  <svg class="front-wave" viewBox="0 0 615 352" aria-hidden="true">
    <defs>
      <linearGradient id="edgeGlow" x1="0" x2="1" y1="0" y2="0">
        <stop offset="0" stop-color="#f7941d" stop-opacity="1"/>
        <stop offset="0.35" stop-color="#f7941d" stop-opacity="0.2"/>
        <stop offset="0.65" stop-color="#f7941d" stop-opacity="0.2"/>
        <stop offset="1" stop-color="#f7941d" stop-opacity="1"/>
      </linearGradient>
    </defs>
    <path fill="url(#edgeGlow)" d="M0 226 C60 268 120 288 190 275 C300 255 360 112 470 72 C530 52 590 54 615 66 L615 352 L0 352 Z"/>
    <path fill="var(--brand-red)" d="M0 235 C60 276 120 295 190 283 C300 263 360 120 470 80 C530 60 590 63 615 76 L615 352 L0 352 Z"/>
  </svg>

  <div class="brand">
    <span class="brand__dot"></span>
    <p class="brand__name">Valcorne<br>Health Care Marketing</p>
  </div>

  <div class="person">
    <p class="person__name">Marla Tenwick</p>
    <p class="person__title">CEO</p>
  </div>

  <ul class="contacts">
    <li class="contacts__item">
      <span>(512)638-2974</span>
      <svg class="contacts__icon" viewBox="0 0 20 20" aria-label="Phone">
        <circle cx="10" cy="10" r="10" fill="var(--gold)"/>
        <path fill="#fff" d="M6.2 5.2l2 -.4 1.1 2.6-1.3 1c.6 1.3 1.5 2.2 2.8 2.8l1-1.3 2.6 1.1-.4 2c-4.4.2-8-3.4-7.8-7.8z"/>
      </svg>
    </li>
    <li class="contacts__item">
      <span>marla@valcorne.com</span>
      <svg class="contacts__icon" viewBox="0 0 20 20" aria-label="Email">
        <circle cx="10" cy="10" r="10" fill="var(--gold)"/>
        <rect x="5" y="6.5" width="10" height="7" rx="1" fill="#fff"/>
        <path d="M5.5 7.2l4.5 3.3 4.5-3.3" fill="none" stroke="var(--gold)" stroke-width="1.1"/>
      </svg>
    </li>
    <li class="contacts__item">
      <span>www.valcorne.com</span>
      <svg class="contacts__icon" viewBox="0 0 20 20" aria-label="Website">
        <circle cx="10" cy="10" r="10" fill="var(--gold)"/>
        <circle cx="10" cy="10" r="5" fill="none" stroke="#fff" stroke-width="1.4"/>
        <path d="M5 10h10M10 5c-2.2 2.8-2.2 7.2 0 10M10 5c2.2 2.8 2.2 7.2 0 10" fill="none" stroke="#fff" stroke-width="1.1"/>
      </svg>
    </li>
  </ul>
</section>

<section class="card card--back">
  <div class="brand">
    <span class="brand__dot"></span>
    <p class="brand__name">Valcorne<br>Health Care Marketing</p>
  </div>
</section>

</body>
</html>
```